Brell Stone Company Business Cards

Front and Back Business Card - logo and text setup - cool design. I need workable photoshop or illustrator files so I can setup each employee card with design that is created
Updates

Hi everyone, thank you for the great entries. Please no more white and blue cards - there are so many already - black and silver only now please. thanks!

Target Market(s)

Construction Industry - Facility Managers

Industry/Entity Type

Construction

Contact Information for Business Card

I really like contemporary simplistic looks - clean neat....not opposed to seeing some black backrounds

Requirements
Must have
• Logo/website address with design on front only - www.brellstone-example.com (logo attached)
• Back:
• Name/Title/Company Address/Phone/email address
Nice to have
• Cool design
Should not have
• Nothing gimmicky like Fire or Water - since we are a Fire Protection company - it has all been done

```html
<!DOCTYPE html>
<html lang="en">
<head>
<meta charset="utf-8">
<title>Brell Stone Company Business Cards</title>
<link href="https://fonts.googleapis.com/css2?family=Source+Sans+3:wght@400;600;800&display=swap" rel="stylesheet">
<style>
  :root {
    --stage-light: #e8e9ea;
    --stage-dark: #cfd0d2;
    --card-dark-start: #242325;
    --card-dark-end: #3a393c;
    --card-light: #ffffff;
    --text-light: #ffffff;
    --text-muted: #e4e4e6;
    --brand-navy: #1f3f7a;
    --text-body: #2a2a2a;
    --rule-blue: #3f78c0;
  }
  html, body {
    margin: 0;
    padding: 0;
    width: 800px;
    height: 1200px;
    overflow: hidden;
  }
  body {
    position: relative;
    font-family: "Source Sans 3", sans-serif;
    background: radial-gradient(ellipse at 50% 50%, var(--stage-light) 0%, var(--stage-dark) 75%);
  }
  .card {
    position: absolute;
    left: 148px;
    width: 504px;
    height: 288px;
    overflow: hidden;
  }
  .card--back {
    top: 170px;
    border-radius: 11px;
    background: linear-gradient(90deg, var(--card-dark-start) 0%, var(--card-dark-end) 100%);
    color: var(--text-light);
  }
  .card--front {
    top: 703px;
    background: var(--card-light);
  }
  .brand-name {
    position: absolute;
    left: 33px;
    top: 40px;
    margin: 0;
    font-weight: 800;
    font-size: 38px;
    line-height: 1;
    letter-spacing: -0.5px;
    color: var(--text-light);
  }
  .brand-watermark {
    position: absolute;
    left: 236px;
    top: 212px;
    font-weight: 800;
    font-size: 64px;
    line-height: 1;
    white-space: nowrap;
    color: rgba(255, 255, 255, 0.05);
  }
  .person-name {
    position: absolute;
    left: 33px;
    top: 143px;
    margin: 0;
    font-weight: 600;
    font-size: 23px;
    line-height: 1;
  }
  .person-title {
    position: absolute;
    left: 33px;
    top: 170px;
    margin: 0;
    font-size: 13px;
    line-height: 1;
    color: var(--text-muted);
  }
  .contact {
    position: absolute;
    left: 33px;
    display: flex;
    align-items: center;
    gap: 6px;
    font-size: 13px;
    line-height: 1;
    color: var(--text-muted);
  }
  .contact--phone { top: 196px; }
  .contact--email { top: 196px; left: 145px; }
  .contact--address { top: 221px; gap: 10px; }
  .contact svg { fill: var(--text-light); display: block; }
  .contact-rule {
    position: absolute;
    left: 33px;
    top: 242px;
    width: 398px;
    height: 1px;
    background: linear-gradient(90deg, var(--rule-blue) 0%, var(--rule-blue) 60%, rgba(255,255,255,0.7) 100%);
  }
  .front-brand {
    position: absolute;
    left: 0;
    right: 0;
    top: 118px;
    margin: 0;
    text-align: center;
    font-weight: 800;
    font-size: 40px;
    line-height: 1;
    letter-spacing: -0.5px;
    color: var(--brand-navy);
  }
  .front-web {
    position: absolute;
    left: 0;
    right: 0;
    top: 198px;
    text-align: center;
    font-size: 14px;
    line-height: 1;
    color: var(--text-body);
  }
</style>
</head>
<body>
  <section class="card card--back" aria-label="Back of business card">
    <div class="brand-watermark" aria-hidden="true">Brell Stone</div>
    <p class="brand-name">Brell Stone Company</p>
    <h1 class="person-name">Daniel Harlow</h1>
    <p class="person-title">Managing Member</p>
    <div class="contact contact--phone">
      <svg width="9" height="10" viewBox="0 0 24 24" aria-hidden="true"><path d="M6.6 10.8a15.1 15.1 0 0 0 6.6 6.6l2.2-2.2a1 1 0 0 1 1-.25 11.4 11.4 0 0 0 3.6.57 1 1 0 0 1 1 1V20a1 1 0 0 1-1 1A17 17 0 0 1 3 4a1 1 0 0 1 1-1h3.5a1 1 0 0 1 1 1c0 1.25.2 2.45.57 3.57a1 1 0 0 1-.25 1z"/></svg>
      <span>0312-555-014</span>
    </div>
    <div class="contact contact--email">
      <svg width="9" height="7" viewBox="0 0 24 18" aria-hidden="true"><path d="M0 0h24v18H0z" opacity=".9"/><path d="M0 0l12 9 12-9" fill="none" stroke="#2f2e31" stroke-width="2"/></svg>
      <span>@yourweb.com</span>
    </div>
    <div class="contact contact--address">
      <svg width="10" height="13" viewBox="0 0 24 32" aria-hidden="true"><path d="M12 0C5.4 0 0 5.3 0 11.8 0 20.6 12 32 12 32s12-11.4 12-20.2C24 5.3 18.6 0 12 0zm0 16.5a4.7 4.7 0 1 1 0-9.4 4.7 4.7 0 0 1 0 9.4z"/></svg>
      <span>your address here</span>
    </div>
    <div class="contact-rule"></div>
  </section>

  <section class="card card--front" aria-label="Front of business card">
    <p class="front-brand">Brell Stone Company</p>
    <p class="front-web">www.brellstone-example.com</p>
  </section>
</body>
</html>
```